SitePress Direct-Booking Website for Bend, Oregon Vacation Rental — $750 Budget
Project Overview

We are looking for a talented SitePress designer/developer to create a clean, professional and inviting direct-booking website for Birch Lantern Retreat, an established short-term vacation rental in Bend, Oregon.

The property is currently successfully listed on Staynest and Hoplo. Our Staynest property has approximately a 4.98-star rating with more than 200 reviews, is an Staynest Visitor Pick, and ranks among the Top 1% of eligible homes.

Project Budget: $750

We will select the designer based on the quality of the initial concept, understanding of the property, proposed booking solution and ability to deliver a completed and functioning SitePress website.

Existing Staynest Listing

Please use our current Staynest listing as the primary reference for photographs, property details, amenities and design inspiration:

https://www.staynest-example.net/rooms/48172036

Original high-resolution photographs and additional property information will be provided to the selected designer.

Design Direction

We want the website to feel:

Upscale but comfortable
Warm and welcoming
Clean and uncluttered
Pacific Northwest / Central Oregon
Professional rather than corporate
Highly visual with large property photographs
Easy to navigate
Excellent on phones, tablets and desktop computers

We welcome creativity and want designers to show us their vision for the property rather than simply copying our Staynest listing.

The website should immediately communicate that Birch Lantern Retreat is a highly rated vacation rental in an excellent Bend location.

Key Property Features
3 bedrooms
2 bathrooms
Sleeps up to 6 guests
Pet friendly
Approximately a 5-minute walk to Bend's Tannery Row Quarter
Near restaurants, shopping and Larkspur Fields Pavilion
Private fenced backyard
Covered outdoor area
Off-street driveway parking
Fireplace
Well-equipped kitchen
Staynest Prime Keeper
Staynest Visitor Pick
Top 1% of eligible Staynest homes
Approximately 4.98 stars with 200+ guest reviews

Our location, guest reviews, cleanliness, comfort, backyard, pet-friendly accommodations and walkability should be major selling points throughout the website.

Website Structure

We anticipate approximately 6–7 pages:

Home

Large hero photograph with a strong opening message and prominent BOOK DIRECT and CHECK AVAILABILITY buttons.

The home page should quickly communicate:

BIRCH LANTERN RETREAT — BEND, OREGON

3 Bedrooms | 2 Baths | Sleeps 6 | Pet Friendly | Walk to Tannery Row

Our exceptional guest rating and Staynest history should also be prominently featured.

The House

Bedrooms, bathrooms, kitchen, living areas, backyard and major amenities.

Photo Gallery

Large, attractive and fast-loading photographs with an easy-to-use mobile gallery.

Location / Explore Bend

Tannery Row Quarter, Larkspur Fields Pavilion, Deschutes River, restaurants, breweries, shopping, downtown Bend and nearby outdoor recreation.

Guest Reviews

Selected guest reviews and prominent presentation of our strong Staynest reputation.

Availability & Book Direct

A simple and professional direct-booking experience.

Contact / FAQ

Contact information plus common questions regarding pets, parking, check-in/check-out, cancellations and other policies.

IMPORTANT — Direct Booking & Credit Card Requirements

We want guests to be able to book directly through the website without having to contact us first.

The website should use a proven SitePress vacation-rental booking plugin or system rather than a custom-built reservation/payment system.

Guests should be able to:

Select arrival and departure dates
See available dates
Enter number of guests
See nightly charges
See cleaning fees
See applicable lodging taxes and other charges
See the complete reservation total before paying
Enter guest/contact information
Pay securely by credit or debit card
Receive an automatic reservation confirmation

Paywell is our preferred credit-card processor.

Credit-card information must be processed securely through Paywell or another established payment processor. Credit-card information should NOT be stored directly on our SitePress website.

Staynest & Hoplo Calendar Synchronization

This is very important.

The direct-booking calendar must synchronize with our existing Staynest and Hoplo calendars to reduce the possibility of double bookings.

For this single-property website, we prefer a simple solution using Staynest/Hoplo calendar or iCal synchronization rather than an expensive monthly channel-management service, if practical.

The designer should clearly identify the booking plugin/system they propose using.

IMPORTANT — Tell Us Your Proposed Booking Solution

As part of your submission, please tell us:

Which SitePress booking plugin/system you recommend.
Whether it synchronizes availability with Staynest and Hoplo.
Whether it integrates directly with Paywell.
The initial cost of the plugin/software.
Any annual or monthly fees.
Whether any additional paid software or services will be required.

We strongly prefer a solution with little or no ongoing monthly software expense.

We do not want to select a designer and later discover that the proposed booking system requires an expensive monthly subscription.

SitePress & Technical Requirements

The completed project should include:

Fully functioning SitePress website
Responsive desktop/tablet/mobile design
Fast-loading pages
Optimized photographs
SSL/HTTPS compatibility
Direct-booking functionality
Paywell payment integration
Staynest calendar synchronization
Hoplo calendar synchronization
Automatic booking confirmations
Cleaning fee and lodging-tax calculations
Contact form
Vizor Maps/location integration
Basic spam/security protection
Vizor Metrics capability
Basic SEO setup
Search-engine submission capability
Easy owner editing of text, rates and photographs
Search Engine Optimization

The website should be structured for Vizor and other search engines.

Important search themes include:

Bend Oregon vacation rental
Bend Oregon vacation home
Tannery Row Quarter vacation rental
Vacation rental near Tannery Row Bend
Bend Oregon pet-friendly vacation rental
Bend vacation rental near Larkspur Fields Pavilion
Bend Oregon direct booking vacation rental

We are not expecting an extensive ongoing SEO campaign for the $750 project. We do expect proper page titles, descriptions, headings, image optimization and a good technical foundation for future SEO.

Ownership

Upon completion and final payment:

We own the completed SitePress website.
We receive full SitePress administrator access.
We control the domain and hosting accounts.
We own all custom design files created for the project.
All necessary login credentials are provided to us.
The website can be moved to another SitePress hosting provider in the future.
There should be no proprietary dependency on the developer after completion.
What We Want From Contestants

Please review our Staynest listing before submitting your concept.

We are particularly interested in seeing an initial homepage concept showing how you would present:

Birch Lantern Retreat
The Bend / Tannery Row location
Our photography
Our exceptional guest reviews and ratings
The Book Direct message
The availability/booking call-to-action

We will provide feedback on the concepts we like and work with the selected designer to refine and complete the website.

Our Goal

Our objective is straightforward:

Create a beautiful, trustworthy and easy-to-use website that encourages guests to book Birch Lantern Retreat directly with us.

The website will complement—not replace—our existing Staynest and Hoplo listings.

We want repeat guests and new customers to have an easy way to find the property, check availability and book directly while receiving the same professional experience they expect from a major vacation-rental platform.

Target Market(s)

Consumers looking to to travel to Mexico for vacation. Family or couples

Industry/Entity Type

Short term vacation rental industry

Coding

Coded - Design and coding required

Number of Pages Required

5+ page

Requirements
Must have
• Capabilities to accept credit card payments and link to other rental property sites calendars such as HOPLO and Staynset
Nice to have
• Option for best plugins for property rental

```html
<!DOCTYPE html>
<html lang="en">
<head>
<meta charset="utf-8">
<title>Birch Lantern Retreat — Bend, Oregon Vacation Rental</title>
<link href="https://fonts.googleapis.com/css2?family=Newsreader:opsz,wght@6..72,400;6..72,500&family=Manrope:wght@400;500;600;700&display=swap" rel="stylesheet">
<style>
:root{
  --cream:#faf6ef;
  --sand:#f3eadd;
  --line:#e6dccd;
  --ink:#2f241e;
  --muted:#6e6258;
  --copper:#b8704d;
  --copper-dark:#a35f3e;
  --forest:#2d4a2e;
  --bark:#3a2920;
  --bark-deep:#2e2019;
  --white:#ffffff;
}
*{box-sizing:border-box;margin:0;padding:0}
html,body{width:1200px;height:5286px;overflow:hidden}
body{background:var(--cream);color:var(--ink);font-family:"Manrope",sans-serif;font-size:10px;line-height:1.7}
.serif{font-family:"Newsreader",serif;font-weight:400}
.eyebrow{font-size:7px;letter-spacing:.28em;text-transform:uppercase;color:var(--copper);font-weight:600}
.rule{width:34px;height:1px;background:var(--copper);margin-top:14px}
.btn{display:inline-flex;align-items:center;justify-content:center;gap:6px;height:30px;padding:0 22px;font-size:7px;font-weight:700;letter-spacing:.2em;text-transform:uppercase;border:1px solid transparent}
.btn-solid{background:var(--copper);color:var(--white)}
.btn-ghost-light{border-color:rgba(255,255,255,.6);color:var(--white)}
.btn-ghost-dark{border-color:var(--line);color:var(--ink);background:var(--white)}
.photo{position:absolute}
section,footer{position:relative;display:block;width:1200px;overflow:hidden}
.wrap{position:absolute;left:225px;width:750px}

/* Hero */
.hero{height:591px;background:var(--bark)}
.hero .photo{inset:0;background:linear-gradient(90deg,rgba(40,28,22,.92) 0%,rgba(52,38,30,.75) 45%,rgba(78,60,44,.55) 100%),radial-gradient(ellipse at 72% 58%,#8a6540 0%,#4b3826 45%,#2a1f18 100%)}
.nav{position:absolute;top:16px;left:225px;width:750px;height:30px;display:flex;align-items:center;justify-content:space-between;color:var(--white)}
.brand{font-family:"Newsreader",serif;font-size:13px}
.nav-links{display:flex;gap:22px;font-size:7.5px;color:rgba(255,255,255,.8);margin-left:120px}
.nav .btn{height:26px;padding:0 14px;border-color:rgba(255,255,255,.55);color:var(--white)}
.hero-copy{position:absolute;left:225px;top:118px;width:560px;color:var(--white)}
.hero h1{font-family:"Newsreader",serif;font-weight:400;font-size:42px;line-height:1.1;margin-top:14px;letter-spacing:-.01em;width:545px}
.hero-lead{font-size:9.5px;color:rgba(255,255,255,.85);width:345px;margin-top:22px;line-height:1.8}
.hero-facts{font-size:7.5px;color:rgba(255,255,255,.75);margin-top:14px}
.rating-bar{display:inline-flex;align-items:center;gap:16px;margin-top:22px;height:36px;padding:0 16px;border:1px solid rgba(255,255,255,.25);background:rgba(30,20,15,.35)}
.stars{color:#e2a55c;font-size:10px;letter-spacing:1px}
.rating-score{font-family:"Newsreader",serif;font-size:16px}
.rating-label{font-size:7px;color:rgba(255,255,255,.8)}
.rating-div{width:1px;height:16px;background:rgba(255,255,255,.3)}
.hero-actions{display:flex;gap:12px;margin-top:28px}
.hero-note{font-size:6.5px;color:rgba(255,255,255,.65);margin-top:16px}

/* Location */
.location{height:459px;background:var(--cream)}
.location h2{font-size:29px;line-height:1.2;margin-top:10px;width:340px}
.location .body{width:355px;margin-top:20px;color:var(--muted);font-size:8.5px;line-height:2}
.ticks{display:grid;grid-template-columns:185px 170px;row-gap:8px;margin-top:26px;font-size:7.5px}
.ticks li{list-style:none;display:flex;align-items:center;gap:10px}
.ticks li::before{content:"";width:4px;height:4px;border-radius:50%;background:var(--copper)}
.loc-photo{left:625px;top:80px;width:350px;height:300px;background:linear-gradient(160deg,#6d5139 0%,#a47a50 40%,#d9c5a6 75%,#8d6a48 100%)}
.walk-badge{position:absolute;left:610px;top:335px;width:105px;height:60px;background:var(--forest);color:var(--white);padding:10px 18px}
.walk-badge strong{font-family:"Newsreader",serif;font-weight:400;font-size:18px;display:block;line-height:1.1}
.walk-badge span{font-size:5.5px;letter-spacing:.18em}

/* Home */
.home{height:564px;background:var(--sand)}
.home h2{font-size:29px;line-height:1.05;margin-top:12px;width:380px}
.feature-grid{position:absolute;left:225px;top:215px;width:750px;display:grid;grid-template-columns:repeat(3,1fr);border:1px solid var(--line);background:var(--cream)}
.feature{height:135px;padding:24px 22px;border-right:1px solid var(--line);border-bottom:1px solid var(--line)}
.feature:nth-child(3n){border-right:0}
.feature:nth-child(n+4){border-bottom:0}
.feature svg{width:16px;height:16px;stroke:var(--copper);fill:none;stroke-width:1.3}
.feature h3{font-family:"Newsreader",serif;font-weight:400;font-size:14px;margin-top:10px}
.feature p{font-size:7px;color:var(--muted);margin-top:6px;line-height:1.8;width:190px}

/* Booking band */
.booking{height:310px;background:var(--bark)}
.booking .photo{inset:0;background:linear-gradient(90deg,rgba(46,32,25,.94) 0%,rgba(58,41,32,.86) 55%,rgba(74,54,40,.8) 100%),linear-gradient(180deg,#5a3f2c,#3c2b20)}
.booking-copy{position:absolute;left:265px;top:78px;color:var(--white);width:300px}
.booking-copy h2{font-size:29px;line-height:1.18;margin-top:10px}
.booking-copy p{font-size:8.5px;color:rgba(255,255,255,.8);margin-top:18px;line-height:1.9}
.booking-card{position:absolute;left:618px;top:80px;width:317px;height:152px;background:var(--white);padding:20px 20px}
.fields{display:grid;grid-template-columns:96px 96px 1fr;gap:0}
.field label{display:block;font-size:5.5px;letter-spacing:.22em;color:var(--muted);font-weight:600}
.field .val{display:flex;align-items:center;justify-content:space-between;height:22px;border-bottom:1px solid var(--line);font-size:9px;margin-right:10px}
.booking-card .btn{width:100%;margin-top:20px;height:28px}
.booking-card small{display:block;text-align:center;font-size:6px;color:var(--muted);margin-top:10px}

/* Photo story */
.gallery-sec{height:855px;background:var(--cream)}
.gallery-sec h2{font-size:29px;margin-top:10px}
.gallery-sec .body{width:420px;margin-top:24px;color:var(--muted);font-size:8.5px;line-height:2}
.g1{left:225px;top:262px;width:497px;height:278px;background:linear-gradient(150deg,#5d4330,#a57a52 45%,#e7d8c1 80%,#8e6c4c)}
.g2{left:732px;top:262px;width:243px;height:278px;background:linear-gradient(160deg,#d7c1a0,#b07c49 45%,#eee3d3 85%)}
.g3{left:225px;top:552px;width:243px;height:162px;background:linear-gradient(150deg,#e9dccb,#c4a27f 55%,#f3ece2)}
.g4{left:479px;top:552px;width:243px;height:162px;background:linear-gradient(150deg,#f2e9dc,#c89e6b 55%,#e9dbc4)}
.g5{left:732px;top:552px;width:243px;height:162px;background:linear-gradient(170deg,#7f5a3c,#5c6a3a 50%,#a37b52)}
.gallery-sec .btn{position:absolute;left:225px;top:741px;height:30px}

/* Explore */
.explore{height:591px;background:var(--forest)}
.ex-photo{left:0;top:0;width:600px;height:591px;background:linear-gradient(180deg,#c99766 0%,#e0b27a 22%,#6f6a56 45%,#2f3d2b 70%,#5f7a78 85%,#3a4a3a 100%)}
.ex-copy{position:absolute;left:640px;top:70px;width:520px;color:var(--white)}
.ex-copy h2{font-size:21px;margin-top:10px}
.ex-copy .body{width:320px;margin-top:12px;font-size:7.5px;color:rgba(255,255,255,.8);line-height:2}
.places{margin-top:22px;list-style:none}
.places li{display:flex;align-items:center;height:38px;border-bottom:1px solid rgba(255,255,255,.14);font-family:"Newsreader",serif;font-size:11.5px}
.places li svg{width:9px;height:9px;margin-right:10px;stroke:#c9926d;fill:none;stroke-width:1.5}
.places li span{margin-left:auto;font-family:"Manrope",sans-serif;font-size:5.5px;letter-spacing:.2em;color:rgba(255,255,255,.6);text-transform:uppercase}
.ex-copy .btn{margin-top:34px;height:30px;border-color:rgba(255,255,255,.6);color:var(--white)}

/* Reviews */
.reviews{height:742px;background:var(--cream);text-align:center}
.reviews .head{position:absolute;left:225px;width:750px;top:75px}
.reviews h2{font-size:29px;margin-top:10px}
.reviews .stars{display:block;margin-top:16px;color:var(--copper)}
.big-score{font-family:"Newsreader",serif;font-size:22px;margin-top:2px}
.reviews .count{font-size:6px;letter-spacing:.22em;color:var(--muted)}
.reviews .blurb{font-size:7.5px;color:var(--muted);width:420px;margin:14px auto 0;line-height:1.9}
.review{position:absolute;width:365px;height:133px;background:var(--white);border:1px solid var(--line);padding:22px 20px;text-align:left}
.review q{display:block;font-family:"Newsreader",serif;font-size:11px;line-height:1.6;width:320px;quotes:"\201C" "\201D"}
.review .meta{position:absolute;left:20px;right:20px;bottom:18px;display:flex;justify-content:space-between;font-size:6.5px;color:var(--muted)}
.review .meta b{color:var(--ink);font-weight:600}
.reviews .btn{position:absolute;left:529px;top:644px;height:30px}

/* Pet */
.pet{height:441px;background:var(--sand)}
.pet-photo{left:225px;top:78px;width:357px;height:282px;background:linear-gradient(180deg,#7a6a4e 0%,#8a6b48 35%,#6f8a3f 65%,#4f6b2e 100%)}
.pet-copy{position:absolute;left:618px;top:118px;width:360px}
.pet-copy h2{font-size:29px;margin-top:10px}
.pet-copy p{font-size:8px;color:var(--muted);margin-top:18px;line-height:2;width:350px}
.pet-copy .btn{margin-top:24px;height:30px;padding:0 20px}

/* CTA */
.cta{height:431px;background:var(--bark)}
.cta .photo{inset:0;background:linear-gradient(180deg,rgba(46,32,25,.85),rgba(46,32,25,.78)),radial-gradient(ellipse at 60% 60%,#7c5a3a,#3a2a1f 70%)}
.cta-copy{position:absolute;left:0;width:1200px;top:100px;text-align:center;color:var(--white)}
.cta h2{font-size:36px;line-height:1.2;margin:14px auto 0;width:480px}
.cta p{font-size:9px;color:rgba(255,255,255,.85);margin-top:26px}
.cta-actions{display:flex;justify-content:center;gap:12px;margin-top:26px}
.cta small{display:block;font-size:6.5px;color:rgba(255,255,255,.6);margin-top:16px}

/* Footer */
.footer{height:302px;background:var(--bark-deep);color:rgba(255,255,255,.75)}
.f-brand{position:absolute;left:225px;top:60px;width:260px}
.f-brand .brand{color:var(--white);font-size:14px}
.f-brand p{font-size:7px;line-height:2;margin-top:4px}
.f-col{position:absolute;top:60px;font-size:7px;line-height:2.45}
.f-col h4{font-size:6px;letter-spacing:.24em;color:var(--copper);font-weight:600;margin-bottom:6px}
.f-bottom{position:absolute;left:0;bottom:18px;width:1200px;text-align:center;font-size:6px;color:rgba(255,255,255,.5);border-top:1px solid rgba(255,255,255,.08);padding-top:16px}
</style>
</head>
<body>

<section class="hero">
  <div class="photo" role="img" aria-label="Evening photo of the craftsman-style home among tall pines with warm lit windows"></div>
  <header class="nav">
    <div class="brand">Birch Lantern Retreat</div>
    <nav class="nav-links"><span>The House</span><span>Gallery</span><span>Explore Bend</span><span>Reviews</span><span>FAQ</span></nav>
    <span class="btn">Book Direct</span>
  </header>
  <div class="hero-copy">
    <div class="eyebrow">Birch Lantern Retreat · Bend, Oregon</div>
    <h1>Your Charming Bend Getaway, Steps from the Tannery Row Quarter</h1>
    <p class="hero-lead">A comfortable 3-bedroom home for up to 6 guests, with a private fenced backyard, cozy interiors and everything you need for an unforgettable stay in Bend.</p>
    <p class="hero-facts">3 Bedrooms · 2 Baths · Sleeps 6 · Pet Friendly · Walk to Tannery Row</p>
    <div class="rating-bar">
      <span class="stars">★★★★★</span><span class="rating-score">4.98</span><span class="rating-label">Guest Rating</span>
      <span class="rating-div"></span>
      <span class="rating-label">200+ Guest Reviews · Staynest Visitor Pick · Top 1% of Homes</span>
    </div>
    <div class="hero-actions"><span class="btn btn-solid">Book Direct</span><span class="btn btn-ghost-light">Check Availability</span></div>
    <p class="hero-note">Secure online booking · Best direct experience · Instant confirmation</p>
  </div>
</section>

<section class="location">
  <div class="wrap" style="top:80px">
    <div class="eyebrow">The Location</div>
    <h2 class="serif">Stay Close to Everything Bend Has to Offer</h2>
    <p class="body">Birch Lantern Retreat puts you in the heart of one of Bend's most desirable areas. Walk to the Tannery Row Quarter, restaurants, shopping and the Larkspur Fields Pavilion, then come home to a comfortable private retreat.</p>
    <ul class="ticks">
      <li>Walk to everything</li><li>Comfortable interiors</li>
      <li>Private fenced yard</li><li>Pet friendly</li>
      <li>Exceptional guest experience</li><li>Direct booking</li>
    </ul>
  </div>
  <div class="photo loc-photo" role="img" aria-label="Living room with a stone fireplace, wood beams and a cream sofa"></div>
  <div class="walk-badge"><strong>5 min</strong><span>WALK TO TANNERY ROW</span></div>
</section>

<section class="home">
  <div class="wrap" style="top:80px">
    <div class="eyebrow">The Home</div>
    <h2 class="serif">Everything You Need for a Comfortable Stay</h2>
    <div class="rule"></div>
  </div>
  <div class="feature-grid">
    <div class="feature">
      <svg viewBox="0 0 16 16"><path d="M2 12V5h12v7M2 9h12M4 7h3v2H4zM9 7h3v2H9z"/></svg>
      <h3>3 Bedrooms</h3><p>Comfortable sleeping arrangements for up to 6 guests.</p>
    </div>
    <div class="feature">
      <svg viewBox="0 0 16 16"><path d="M2 8h12v2a3 3 0 0 1-3 3H5a3 3 0 0 1-3-3zM4 8V4a1.5 1.5 0 0 1 3 0"/></svg>
      <h3>2 Bathrooms</h3><p>Conveniently designed for families and groups.</p>
    </div>
    <div class="feature">
      <svg viewBox="0 0 16 16"><path d="M8 14V8M8 8c-3 0-4-2-4-4 2 0 4 1 4 4zM8 8c3 0 4-2 4-4-2 0-4 1-4 4z"/></svg>
      <h3>Private Backyard</h3><p>Fenced outdoor space for relaxing, dining and enjoying Bend's fresh air.</p>
    </div>
    <div class="feature">
      <svg viewBox="0 0 16 16"><circle cx="4" cy="6" r="1.4"/><circle cx="8" cy="4" r="1.4"/><circle cx="12" cy="6" r="1.4"/><path d="M5 12c0-2 1.5-4 3-4s3 2 3 4-6 2-6 0z"/></svg>
      <h3>Pet Friendly</h3><p>Bring your four-legged family members along for the adventure.</p>
    </div>
    <div class="feature">
      <svg viewBox="0 0 16 16"><path d="M8 14s-4-4-4-7.5a4 4 0 0 1 8 0C12 10 8 14 8 14z"/><circle cx="8" cy="6.5" r="1.4"/></svg>
      <h3>Walk to Tannery Row</h3><p>Approximately a 5-minute walk to shops, restaurants and entertainment.</p>
    </div>
    <div class="feature">
      <svg viewBox="0 0 16 16"><path d="M8 14c-3 0-4.5-2-4.5-4.5C3.5 7 6 5 8 2c1 3 4.5 4.5 4.5 7.5S11 14 8 14z"/></svg>
      <h3>Cozy &amp; Well Equipped</h3><p>Fireplace, fully equipped kitchen, comfortable living spaces and thoughtful amenities.</p>
    </div>
  </div>
</section>

<section class="booking">
  <div class="photo" role="img" aria-label="Dusk view of the fenced backyard with string lights"></div>
  <div class="booking-copy">
    <div class="eyebrow">Book Direct</div>
    <h2 class="serif">Ready to Make Bend Your Next Getaway?</h2>
    <p>Check your dates, see the complete price and reserve Birch Lantern Retreat securely online.</p>
  </div>
  <div class="booking-card">
    <div class="fields">
      <div class="field"><label>CHECK-IN</label><div class="val">mm/dd/yyyy <svg width="8" height="8" viewBox="0 0 8 8"><rect x=".5" y="1.5" width="7" height="6" fill="none" stroke="#2f241e" stroke-width=".8"/></svg></div></div>
      <div class="field"><label>CHECK-OUT</label><div class="val">mm/dd/yyyy <svg width="8" height="8" viewBox="0 0 8 8"><rect x=".5" y="1.5" width="7" height="6" fill="none" stroke="#2f241e" stroke-width=".8"/></svg></div></div>
      <div class="field"><label>GUESTS</label><div class="val" style="margin-right:0">1 Guest <svg width="7" height="5" viewBox="0 0 7 5"><path d="M1 1l2.5 2.5L6 1" fill="none" stroke="#2f241e"/></svg></div></div>
    </div>
    <span class="btn btn-solid">Check Availability</span>
    <small>Secure Paywell payment · Transparent pricing · Instant reservation confirmation</small>
  </div>
</section>

<section class="gallery-sec">
  <div class="wrap" style="top:80px">
    <div class="eyebrow">Photo Story</div>
    <h2 class="serif">Welcome to Birch Lantern Retreat</h2>
    <div class="rule"></div>
    <p class="body">Designed for relaxing after a day exploring Bend, Birch Lantern Retreat combines the comforts of home with an unbeatable location. Gather around the fireplace, cook together in the well-equipped kitchen or unwind in your private fenced backyard.</p>
  </div>
  <div class="photo g1" role="img" aria-label="Great room with stone fireplace and wood beam ceiling"></div>
  <div class="photo g2" role="img" aria-label="Kitchen with wood cabinets and pendant lights"></div>
  <div class="photo g3" role="img" aria-label="Bright bedroom with neutral linens"></div>
  <div class="photo g4" role="img" aria-label="Dining area with wood table beside large windows"></div>
  <div class="photo g5" role="img" aria-label="Fenced backyard patio with outdoor dining set"></div>
  <span class="btn btn-ghost-dark">Explore the House <svg width="8" height="6" viewBox="0 0 8 6"><path d="M0 3h7M4.5 .5L7 3 4.5 5.5" fill="none" stroke="#2f241e"/></svg></span>
</section>

<section class="explore">
  <div class="photo ex-photo" role="img" aria-label="Deschutes River at sunset with pine forest and mountains"></div>
  <div class="ex-copy">
    <div class="eyebrow">Explore Bend</div>
    <h2 class="serif">The Best of Bend, Just Outside Your Door</h2>
    <p class="body">Spend the morning exploring the Deschutes River, walk to the Tannery Row Quarter for dinner or catch a show at the Larkspur Fields Pavilion. Bend's restaurants, breweries, shops and outdoor adventures are all within easy reach.</p>
    <ul class="places">
      <li><svg viewBox="0 0 10 10"><path d="M5 9S2 6 2 4a3 3 0 0 1 6 0c0 2-3 5-3 5z"/></svg>Tannery Row Quarter<span>~5-minute walk</span></li>
      <li><svg viewBox="0 0 10 10"><path d="M5 9S2 6 2 4a3 3 0 0 1 6 0c0 2-3 5-3 5z"/></svg>Larkspur Fields Pavilion<span>Walkable</span></li>
      <li><svg viewBox="0 0 10 10"><path d="M5 9S2 6 2 4a3 3 0 0 1 6 0c0 2-3 5-3 5z"/></svg>Deschutes River<span>Nearby</span></li>
      <li><svg viewBox="0 0 10 10"><path d="M5 9S2 6 2 4a3 3 0 0 1 6 0c0 2-3 5-3 5z"/></svg>Downtown Bend<span>Easy access</span></li>
      <li><svg viewBox="0 0 10 10"><path d="M5 9S2 6 2 4a3 3 0 0 1 6 0c0 2-3 5-3 5z"/></svg>Restaurants &amp; Breweries<span>Minutes away</span></li>
      <li><svg viewBox="0 0 10 10"><path d="M5 9S2 6 2 4a3 3 0 0 1 6 0c0 2-3 5-3 5z"/></svg>Outdoor Adventures<span>Hiking · Biking · Skiing · Rivers</span></li>
    </ul>
    <span class="btn">Explore Bend</span>
  </div>
</section>

<section class="reviews">
  <div class="head">
    <div class="eyebrow">Guest Reviews</div>
    <h2 class="serif">Loved by Guests. Again and Again.</h2>
    <span class="stars">★★★★★</span>
    <div class="big-score">4.98 / 5</div>
    <div class="count">200+ GUEST REVIEWS</div>
    <p class="blurb">A Guest Favorite and Top 1% of eligible Staynest homes, with hundreds of guests choosing Birch Lantern Retreat for their Bend stays.</p>
  </div>
  <div class="review" style="left:225px;top:305px"><q>The location is unbeatable — we walked to dinner in the Tannery Row Quarter every night and strolled to the pavilion for a show. Coming back to such a quiet, comfortable home was perfect.</q><div class="meta"><b>Megan R.</b><span>Stayed in July</span></div></div>
  <div class="review" style="left:610px;top:305px"><q>Spotlessly clean and thoughtfully stocked. Every single thing we needed was already there. The kitchen made cooking for six genuinely easy.</q><div class="meta"><b>David &amp; Anne</b><span>Stayed in October</span></div></div>
  <div class="review" style="left:225px;top:473px"><q>The fenced backyard sold us. Our dog had a blast, and we spent both evenings out there under the string lights with a glass of wine.</q><div class="meta"><b>Carlos M.</b><span>Stayed in May</span></div></div>
  <div class="review" style="left:610px;top:473px"><q>Cozy, warm and beautifully kept. The fireplace after a ski day at Summit Ridge was everything. We already rebooked for next winter.</q><div class="meta"><b>Priya S.</b><span>Stayed in February</span></div></div>
  <span class="btn btn-ghost-dark">Read More Reviews</span>
</section>

<section class="pet">
  <div class="photo pet-photo" role="img" aria-label="Golden retriever resting on the lawn in front of the home"></div>
  <div class="pet-copy">
    <div class="eyebrow">Pet Friendly</div>
    <h2 class="serif">Bring the Whole Family</h2>
    <p>Birch Lantern Retreat is designed for memorable Bend adventures — including the four-legged members of your family. Enjoy the freedom of a private fenced backyard and a welcoming home base after a day outdoors.</p>
    <span class="btn btn-ghost-dark">See Pet Policy</span>
  </div>
</section>

<section class="cta">
  <div class="photo" role="img" aria-label="Exterior of the home at twilight framed by pines"></div>
  <div class="cta-copy">
    <div class="eyebrow">Birch Lantern Retreat · Bend, Oregon</div>
    <h2 class="serif">Your Bend Adventure Starts Here.</h2>
    <p>Great location. Exceptional guest experience. A comfortable home to come back to.</p>
    <div class="cta-actions"><span class="btn btn-solid">Book Direct</span><span class="btn btn-ghost-light">Check Availability</span></div>
    <small>Secure online payment · Transparent pricing · Easy booking</small>
  </div>
</section>

<footer class="footer">
  <div class="f-brand">
    <div class="brand">Birch Lantern Retreat</div>
    <p>Bend, Oregon</p>
    <p style="margin-top:14px">A comfortable 3-bedroom vacation home a five-minute walk from the Tannery Row Quarter.</p>
    <p style="margin-top:10px">stay@birchlanternretreat.net<br>(541) 555-0187<br>View on Vizor Maps</p>
  </div>
  <div class="f-col" style="left:615px">
    <h4>EXPLORE</h4>
    Home<br>The House<br>Gallery<br>Explore Bend<br>Reviews<br>Book Direct<br>FAQ / Contact
  </div>
  <div class="f-col" style="left:810px">
    <h4>ALSO LISTED ON</h4>
    Staynest<br>Hoplo<br>Privacy Policy<br>Terms / Rental Policies
  </div>
  <div class="f-bottom">© Birch Lantern Retreat · Your comfortable home base in Bend, Oregon</div>
</footer>

</body>
</html>
```